Business Card Design

I already have a company logo for my company. I have a logo for the manufacturer we represent. I want a professional business card design.

```html
<!DOCTYPE html>
<html lang="en">
<head>
<meta charset="utf-8">
<title>Halden Signal Co. – Business Card</title>
<link href="https://fonts.googleapis.com/css2?family=Montserrat:wght@400;500;700&display=swap" rel="stylesheet">
<style>
  :root {
    --backdrop: #c9c9c9;
    --card-white: #ffffff;
    --card-black: #1c1c1c;
    --brand-red: #e3232b;
    --ink: #2a2a2a;
    --ink-soft: #444444;
    --back-mark: #d9d9d9;
  }
  * { box-sizing: border-box; margin: 0; padding: 0; }
  html, body {
    width: 1200px; height: 900px; overflow: hidden;
    background: var(--backdrop);
    font-family: "Montserrat", sans-serif;
  }
  .stage { position: relative; width: 1200px; height: 900px; }
  .card {
    position: absolute; left: 285px;
    width: 630px; height: 360px;
    border-radius: 22px; overflow: hidden;
  }
  .card-front { top: 60px; background: var(--card-white); }
  .card-back { top: 480px; background: var(--card-black); }

  .front-band { position: absolute; inset: 0; }

  .company-name {
    position: absolute; top: 26px; right: 40px;
    font-weight: 700; font-size: 22px; letter-spacing: 1px;
    color: var(--brand-red); text-transform: uppercase;
    display: flex; align-items: center; gap: 10px;
  }
  .company-name .mark-dot {
    width: 14px; height: 14px; border-radius: 50%;
    background: var(--brand-red);
  }

  .address {
    position: absolute; left: 70px; top: 206px;
    font-size: 15px; line-height: 1.35; color: var(--ink);
  }
  .contact-list {
    position: absolute; left: 46px; top: 266px;
    list-style: none; font-size: 15px; line-height: 1.35; color: var(--ink);
  }
  .contact-list li { display: flex; align-items: center; gap: 10px; }
  .contact-list svg { width: 14px; height: 14px; flex: none; }

  .back-name {
    position: absolute; inset: 0;
    display: flex; align-items: center; justify-content: center; gap: 14px;
    font-weight: 700; font-size: 40px; letter-spacing: 2px;
    color: var(--back-mark); text-transform: uppercase;
  }
  .back-name .mark-square { width: 22px; height: 22px; background: var(--brand-red); }
</style>
</head>
<body>
<main class="stage">
  <section class="card card-front">
    <svg class="front-band" width="630" height="360" viewBox="0 0 630 360">
      <polygon points="0,118 630,68 630,104 0,154" fill="var(--brand-red)"/>
      <g transform="rotate(-4.5 24 143)">
        <text x="24" y="143" fill="#ffffff" font-family="Montserrat, sans-serif" font-weight="700" font-size="22">Marek Ellison</text>
        <text x="26" y="176" fill="var(--ink-soft)" font-family="Montserrat, sans-serif" font-weight="400" font-size="14">Managing Director</text>
      </g>
    </svg>

    <div class="company-name"><span class="mark-dot"></span>Halden Signal Co.</div>

    <p class="address">2140 Quarry Lane<br>Aspen Falls, CO 80490</p>

    <ul class="contact-list">
      <li>
        <svg viewBox="0 0 16 16"><path d="M3 1h3l1 4-2 1a9 9 0 0 0 5 5l1-2 4 1v3a2 2 0 0 1-2 2A13 13 0 0 1 1 3a2 2 0 0 1 2-2z" fill="var(--brand-red)"/></svg>
        555.214.0372
      </li>
      <li>
        <svg viewBox="0 0 16 16"><rect x="1" y="3" width="14" height="10" rx="1" fill="var(--brand-red)"/><path d="M1 4l7 5 7-5" stroke="#fff" stroke-width="1.4" fill="none"/></svg>
        info@haldensignal.com
      </li>
      <li>
        <svg viewBox="0 0 16 16"><circle cx="8" cy="8" r="7" fill="var(--brand-red)"/><path d="M1 8h14M8 1c3 3 3 11 0 14M8 1c-3 3-3 11 0 14" stroke="#fff" stroke-width="1" fill="none"/></svg>
        www.haldensignal.com
      </li>
    </ul>
  </section>

  <section class="card card-back">
    <div class="back-name"><span class="mark-square"></span>Halden Signal Co.</div>
  </section>
</main>
</body>
</html>
```